Web Design Project - Shipping Industry

Goals and Objectives
The objective of the new website is to create a more modern look and feel. The site will also allow for a more effective means of communicating with members while providing the public with information and developments in the local, regional and international shipping industry.
Scope
The website will highlight the history of the organisation inclusive of text and photographs. It will take visitors through the years from beginning to present. Information on the history of the shipping industry will also be included.
It will feature current articles on the organisation, its members and stakeholders in the shipping industry. Member information as well as pertinent details regarding the organisation’s subsidiaries will be documented for the website.
Information as it relates to shipping statistics, case studies, laws and regulations, international treaties and trade documents, shipping terms, careers in shipping, job opportunities, training opportunities, information for shippers including port listing and trade lanes will be main features of the content for the website.
The Association’s community involvement, industry calendar events and related links relevant industry members will also be featured.
Target Market
• The General Public;
• Members of the organization;
• Shipping Industry Stakeholders (local, regional and international);
• Tertiary students conducting research.
• Potential employees
• Potential Business Partners
Best Practice Bench Marketing
The following websites are being looked at:
• Korvel Quayworks - http://www.korvelquayworks.example/ (preferred look)
• Tessaly Maritime Association - http://www.tma-freight.example/ (like image transition on main page)
• Drovna - http://www.drovna.example (professional look)
• PLW - http://www.pelworth.example (preferred color: blue in logo)
• Quillo - http://www.quillo.example/electronics/tv-video-audio/ (preferred look for links page: image + short text below + visit site link)
Expected Result
• 3 - 5 pages which must include: [1] main page [2] standard page [3] links page

```html
<!DOCTYPE html>
<html lang="en">
<head>
<meta charset="utf-8">
<title>The Maritime Guild of Calloway</title>
<link href="https://fonts.googleapis.com/css2?family=Arimo:wght@400;700&family=Roboto+Condensed:wght@500;700&display=swap" rel="stylesheet">
<style>
:root{
  --blue:#1a5fb4;
  --blue-dark:#0e4a99;
  --blue-light:#e6eef8;
  --lime:#c2cc0a;
  --lime-dark:#9aa300;
  --olive:#7d8c00;
  --text:#333;
  --muted:#555;
  --heading:#2b2b2b;
  --dash:#9a9a9a;
  --footer:#0d0d0d;
  --photo-sea:linear-gradient(180deg,#b9cfe6 0%,#8fb0d2 45%,#3b4a5c 72%,#3d6f86 100%);
}
*{box-sizing:border-box;margin:0;padding:0}
html,body{width:801px;height:1200px;overflow:hidden;background:#fff}
body{position:relative;font-family:Arimo,Arial,sans-serif;color:var(--text)}
.abs{position:absolute}
.top-strip{left:0;top:0;width:801px;height:6px;background:#111}
.brand{left:9px;top:14px;display:flex;align-items:center;gap:8px}
.brand-mark{width:14px;height:14px;border-radius:50%;background:var(--blue)}
.brand-name{font-size:17px;color:var(--blue-dark);font-weight:400}
.contact-bar{left:551px;top:6px;width:240px;height:29px;background:var(--blue);border-radius:0 0 4px 4px;display:flex;align-items:center;justify-content:center;gap:14px;color:#fff;font-size:12.5px}
.contact-bar span{display:flex;align-items:center;gap:6px}
.nav{left:110px;top:50px;width:681px;height:36px;background:linear-gradient(#2a74c8,#1657a6);display:flex}
.nav a{color:#fff;text-decoration:none;font-size:13px;padding:0 14px;display:flex;align-items:center;border-right:1px solid #0e4489}
.nav a.active{background:linear-gradient(#d4dc1a,#a7b000);color:#222}
.hero{left:9px;top:98px;width:782px;height:366px;background:var(--photo-sea);border-radius:3px}
.dots{left:371px;top:446px;display:flex;gap:4px}
.dots i{width:9px;height:9px;border-radius:50%;background:#222}
.dots i:first-child{background:#fff}
.login{left:570px;top:110px;width:209px;height:169px}
.login .tabs{display:flex;gap:2px;height:27px}
.login .tab{padding:0 8px;font-size:11.5px;font-weight:700;display:flex;align-items:center;border-radius:3px 3px 0 0;background:#d5dde6;color:#333}
.login .tab.on{background:var(--blue-light);color:var(--blue-dark)}
.login .body{background:var(--blue-light);height:142px;padding:10px 12px;border-radius:0 3px 3px 3px;font-size:11px;color:#333}
.login input{display:block;width:184px;height:21px;border:1px solid #9cc0e8;border-radius:2px;margin:5px 0 13px;background:#fff}
.login .row{display:flex;align-items:center;gap:8px}
.btn-blue{background:var(--blue);color:#fff;font-size:11.5px;padding:4px 8px;border-radius:2px}
.login .forgot{font-size:9.5px;color:var(--blue)}
h2{font-family:"Roboto Condensed",Arial,sans-serif;font-weight:500;font-size:16.5px;color:var(--heading);position:absolute}
h3{font-family:Arimo,Arial,sans-serif;font-weight:400;font-size:14px;color:#444;position:absolute}
.rule{position:absolute;height:0;border-top:1px dashed var(--dash)}
.photo{position:absolute;border:1px solid #ccc}
.intro-photo{left:9px;top:510px;width:137px;height:128px;background:linear-gradient(160deg,#dfe6ee,#b57a4e 60%,#45617a)}
.intro{left:156px;top:510px;width:458px;font-size:9.8px;line-height:16.8px;color:#444}
.more{position:absolute;font-size:11px;color:var(--olive)}
.more.dark{color:#333}
.news-title{position:absolute;font-size:9.8px;font-weight:700;color:#111}
.thumb{position:absolute;width:80px;height:54px;background:linear-gradient(180deg,#a9bdd3,#6b7f95 50%,#2e3e5a);border:1px solid #ccc}
.news-text{position:absolute;width:210px;font-size:9.5px;line-height:14.4px;color:#444}
.partner{position:absolute;width:120px;height:90px;background:#fff;border:1px solid #ddd;box-shadow:0 0 4px rgba(0,0,0,.15) inset;display:flex;align-items:center;justify-content:center;gap:5px;font-size:12px;font-weight:700;color:var(--blue-dark)}
.partner b{width:9px;height:9px;background:var(--blue-dark);display:inline-block}
.side-photo{position:absolute;left:631px;width:159px;height:90px;border:1px solid #bbb}
.side-text{position:absolute;left:631px;width:159px;font-size:9.5px;line-height:14.4px;color:#555}
.btn-lime{position:absolute;left:721px;width:69px;height:24px;background:linear-gradient(#d4dc1a,#a7b000);font-size:11px;color:#222;display:flex;align-items:center;justify-content:center}
.footer{left:0;top:1164px;width:801px;height:36px;background:var(--footer);color:#888;font-size:9.8px}
.social{position:absolute;top:8px;width:19px;height:19px;border-radius:2px;background:#3c7fd0}
.footer-links{position:absolute;left:314px;top:13px}
.copy{position:absolute;right:9px;top:13px}
</style>
</head>
<body>
<div class="abs top-strip"></div>

<header>
  <div class="abs brand"><span class="brand-mark"></span><span class="brand-name">the maritime guild of calloway</span></div>
  <div class="abs contact-bar">
    <span><svg width="15" height="10" viewBox="0 0 15 10"><rect x=".5" y=".5" width="14" height="9" fill="none" stroke="#fff"/><path d="M.5 .5 7.5 6 14.5 .5" fill="none" stroke="#fff"/></svg>info@calloway.example</span>
    <span><svg width="11" height="11" viewBox="0 0 11 11"><path d="M2 0 4 3 3 4.5Q4.5 7 6.5 8L8 7l3 2-1 2Q4 10 0 2Z" fill="#fff"/></svg>555-010-1234</span>
  </div>
  <nav class="abs nav">
    <a class="active">Home</a><a>Shipping Statistics</a><a>Case Studies</a><a>Career</a><a>Jobs</a><a>Contact</a>
  </nav>
</header>

<section>
  <div class="abs hero" role="img" aria-label="Container ship loaded with cargo at sea"></div>
  <div class="abs dots"><i></i><i></i><i></i><i></i><i></i></div>
  <form class="abs login">
    <div class="tabs"><span class="tab on">Login</span><span class="tab">Register</span></div>
    <div class="body">
      User ID :<input type="text">
      Password :<input type="password">
      <div class="row"><span class="btn-blue">Login</span><span class="forgot">forgot password?</span></div>
    </div>
  </form>
</section>

<main>
  <h2 style="left:9px;top:478px">Welcome to Shipping</h2>
  <div class="rule" style="left:9px;top:503px;width:245px"></div>
  <div class="photo intro-photo" role="img" aria-label="Port worker in hard hat at the docks"></div>
  <p class="abs intro">Founded in 1939 as a registered employers' trade union, the Maritime Guild of Calloway (PLW) represents 78 companies in the private sector of the island's shipping industry, and stands ready to forge additional alliances with key partners in the international industry. Membership includes shipping agents, wharf owners, terminal operators and stevedoring companies; together with ship owners and operators. The Maritime Guild manages the supply of labour at Port Ardwell. The PLW deals with all matters affecting the interest of its membership including industrial relations, security and training and</p>
  <span class="more" style="left:556px;top:619px">Read more</span>

  <h2 style="left:9px;top:647px">News</h2>
  <div class="rule" style="left:9px;top:670px;width:607px"></div>

  <h3 style="left:9px;top:677px">Local</h3>
  <div class="news-title" style="left:9px;top:696px">Calloway Opens Bid For Port Community System</div>
  <div class="thumb" style="left:9px;top:714px" role="img" aria-label="Cargo ship at port"></div>
  <p class="news-text" style="left:96px;top:711px">The Harbour Board of Calloway (HBC) has launched the first of a two-stage tender process for the establishment of a Port Community System in Calloway. ...</p>
  <span class="more dark" style="left:246px;top:779px">Read more</span>

  <div class="news-title" style="left:320px;top:696px">Calloway Opens Bid For Port Community System</div>
  <div class="thumb" style="left:320px;top:714px" role="img" aria-label="Cargo ship at port"></div>
  <p class="news-text" style="left:406px;top:711px">The Harbour Board of Calloway (HBC) has launched the first of a two-stage tender process for the establishment of a Port Community System in Calloway. ...</p>
  <span class="more dark" style="left:556px;top:779px">Read more</span>

  <h3 style="left:9px;top:805px">International</h3>
  <div class="news-title" style="left:9px;top:824px">Calloway Opens Bid For Port Community System</div>
  <div class="thumb" style="left:9px;top:842px" role="img" aria-label="Cargo ship at port"></div>
  <p class="news-text" style="left:96px;top:839px">The Harbour Board of Calloway (HBC) has launched the first of a two-stage tender process for the establishment of a Port Community System in Calloway. ...</p>
  <span class="more dark" style="left:246px;top:907px">Read more</span>

  <div class="news-title" style="left:320px;top:824px">Calloway Opens Bid For Port Community System</div>
  <div class="thumb" style="left:320px;top:842px" role="img" aria-label="Cargo ship at port"></div>
  <p class="news-text" style="left:406px;top:839px">The Harbour Board of Calloway (HBC) has launched the first of a two-stage tender process for the establishment of a Port Community System in Calloway. ...</p>
  <span class="more dark" style="left:556px;top:907px">Read more</span>

  <h2 style="left:9px;top:931px">Links</h2>
  <div class="rule" style="left:9px;top:954px;width:607px"></div>
  <div class="partner" style="left:53px;top:962px"><b></b>Tidewell Marine</div>
  <div class="partner" style="left:186px;top:962px"><b></b>Ardwell Wharves</div>
  <div class="partner" style="left:318px;top:962px"><b></b>Cargo Keepers</div>
  <div class="partner" style="left:451px;top:962px"><b></b>Solent Line</div>
  <div class="partner" style="left:53px;top:1066px"><b></b>Varo</div>
  <div class="partner" style="left:186px;top:1066px"><b></b>BlueHold</div>
  <div class="partner" style="left:318px;top:1066px"><b></b>Claimsmark</div>
  <div class="partner" style="left:451px;top:1066px"><b></b>Portlogic</div>
</main>

<aside>
  <h2 style="left:631px;top:478px">Corporate video</h2>
  <div class="side-photo" style="top:503px;background:linear-gradient(180deg,#cfe0f0,#7f9bb8 55%,#34465c)" role="img" aria-label="Container ship video still"></div>
  <p class="side-text" style="top:599px">Lorem Ipsum is simply dummy text of the printing and typesetting</p>
  <span class="btn-lime" style="top:633px">Read more</span>

  <h2 style="left:631px;top:666px">Careers</h2>
  <div class="side-photo" style="top:690px;background:linear-gradient(135deg,#e8e4d8,#b9a58f 50%,#6f7f95)" role="img" aria-label="Team of professionals in a meeting"></div>
  <p class="side-text" style="top:786px">Lorem Ipsum is simply dummy text of the printing and typesetting</p>
  <span class="btn-lime" style="top:820px">Read more</span>

  <h2 style="left:631px;top:853px">Terminals</h2>
  <div class="side-photo" style="top:878px;background:linear-gradient(180deg,#dbe8f5,#8db2d8 55%,#4f86b8)" role="img" aria-label="Container terminal with cranes and ship"></div>
  <p class="side-text" style="top:973px">Lorem Ipsum is simply dummy text of the printing and typesetting</p>
  <span class="btn-lime" style="top:1007px">Read more</span>
</aside>

<footer class="abs footer">
  <span class="social" style="left:9px" aria-label="Social link"></span>
  <span class="social" style="left:32px" aria-label="Social link"></span>
  <span class="social" style="left:55px" aria-label="Social link"></span>
  <span class="footer-links">Laws and regulation &nbsp;|&nbsp; Shipping terms</span>
  <span class="copy">copyrigth © All Rights Reserved</span>
</footer>
</body>
</html>
```